The most modern business card ever !!!

Our company call “Vendalo”. Vendalo is a technology company specialized in cruises solutions. Out main product is a platform to reserve cruises. This is a revolutionary platform that make easier to travel agencies and final users to reserve cruises across dozen companies like tibba, wernu, hpv, dgb, etc..We are a “start up”, with a young team of developers and we want to transmit it.. For it, we want something different, a modern business card that represent cruises and technology.. When someone receive this card, this person should say: wowww this is different… this is modern… this is a cruise related company..
- diferent, modern
- traditions business card

```html
<!DOCTYPE html>
<html lang="en">
<head>
<meta charset="utf-8">
<title>Vendalo Business Card</title>
<link href="https://fonts.googleapis.com/css2?family=Roboto+Condensed:wght@300;400;500&display=swap" rel="stylesheet">
<style>
  :root{
    --bg:#ece9e4;
    --card:#ffffff;
    --ink:#16181b;
    --ink-soft:#3a3d42;
    --accent:#1a9ad6;
    --sky-top:#8fd0f2;
    --sky-mid:#c9ebf8;
    --sea:#4f9fd0;
    --hull:#dfeeea;
  }
  *{box-sizing:border-box;margin:0;padding:0}
  html,body{width:1200px;height:1200px;overflow:hidden}
  body{background:var(--bg);font-family:"Roboto Condensed",sans-serif;color:var(--ink);position:relative}
  .card{position:absolute;left:150px;width:900px;height:514px;background:var(--card);overflow:hidden;box-shadow:0 6px 18px rgba(0,0,0,.12)}
  .card--front{top:64px}
  .card--back{top:622px}

  .brand{position:absolute;font-weight:500;color:var(--ink);letter-spacing:.08em;line-height:1;white-space:nowrap;z-index:2}

  /* front */
  .front__photo{position:absolute;right:0;bottom:0;width:62%;height:62%;
    background:
      radial-gradient(ellipse at 60% 70%, var(--hull) 0 22%, transparent 45%),
      linear-gradient(180deg, rgba(201,235,248,0) 0%, var(--sky-mid) 30%, #bfe2ee 62%, var(--sea) 100%);
    -webkit-mask-image:linear-gradient(90deg,transparent 0%,#000 22%);
            mask-image:linear-gradient(90deg,transparent 0%,#000 22%)}
  .front__halo{position:absolute;left:340px;top:150px;width:560px;height:560px;border-radius:50%;
    background:radial-gradient(circle, rgba(210,236,246,.55), rgba(210,236,246,.15) 70%, transparent 72%)}
  .brand--front{right:70px;top:62px;font-size:112px}
  .contact{position:absolute;left:70px;top:180px;z-index:2}
  .contact__name{font-size:34px;font-weight:400;color:var(--accent);line-height:1.1}
  .contact__role{font-size:17px;color:var(--ink-soft);margin:2px 0 18px}
  .contact__list{list-style:none}
  .contact__item{display:flex;align-items:center;gap:12px;font-size:22px;color:var(--ink-soft);margin-bottom:6px}
  .contact__item svg{width:16px;height:16px;fill:var(--accent);flex:none}
  .contact__tollfree{font-size:30px;color:var(--accent);margin-top:14px}

  /* back */
  .back__photo{position:absolute;inset:0;
    background:
      radial-gradient(ellipse at 28% 62%, var(--hull) 0 18%, transparent 34%),
      linear-gradient(180deg, var(--sky-top) 0%, var(--sky-mid) 45%, rgba(255,255,255,0) 80%),
      linear-gradient(180deg, transparent 62%, var(--sea) 100%);
    -webkit-mask-image:linear-gradient(100deg,#000 35%,transparent 70%);
            mask-image:linear-gradient(100deg,#000 35%,transparent 70%)}
  .brand--back{left:450px;top:170px;font-size:96px}
  .address{position:absolute;left:420px;top:295px;font-size:30px;color:var(--ink-soft);line-height:1.35;font-weight:300;z-index:2}
</style>
</head>
<body>
  <section class="card card--front">
    <div class="front__halo"></div>
    <div class="front__photo" role="img" aria-label="Photo of a white cruise ship sailing on blue sea under a pale sky"></div>
    <div class="brand brand--front">Vendalo</div>
    <div class="contact">
      <p class="contact__name">Marco Lenti</p>
      <p class="contact__role">Director</p>
      <ul class="contact__list">
        <li class="contact__item"><svg viewBox="0 0 16 16"><rect x="4" y="1" width="8" height="14" rx="1.5"/></svg>1-555-018273</li>
        <li class="contact__item"><svg viewBox="0 0 16 16"><circle cx="8" cy="8" r="7"/><path d="M1 8h14M8 1c3 3 3 11 0 14M8 1c-3 3-3 11 0 14" stroke="#fff" stroke-width="1" fill="none"/></svg>www.vendalo.com</li>
        <li class="contact__item"><svg viewBox="0 0 16 16"><rect x="1" y="3" width="14" height="10" rx="1"/><path d="M1 4l7 5 7-5" stroke="#fff" stroke-width="1.2" fill="none"/></svg>marco@vendalo.com</li>
      </ul>
      <p class="contact__tollfree">Toll Free: 1-555-018273</p>
    </div>
  </section>

  <section class="card card--back">
    <div class="back__photo" role="img" aria-label="Photo of a large white cruise ship cutting through waves under a light blue sky"></div>
    <div class="brand brand--back">Vendalo</div>
    <p class="address">Dummy city<br>Dummy Country Land</p>
  </section>
</body>
</html>
```